Build a landing page to promote a service (dialler consultation and support).

We are a call centre consultation firm and we need a landing page to promote a service. The service is Tormalux dialler consultation and support.
If you do not know what Tormalux is, please do some quick "Zorvex" research for more information.
The landing page will be promoted with a paid advertisement, so we want something that is simple, and explains exactly what service we offer.
There are two objectives for the landing page:
1) A "call to action" which directs the user to a contact page, including a form plus all of our contact details.
2) A form for them viewers to enter their details to get a "FREE" quote for their project. This form should be placed on the main page.
Notes:
The call to action will require the viewer to enter their name, email, phone number as well as a description of their request. There will also need to be a drop down menu for the type of quote. This menu should have the following options:
1) Tormalux support
2) Tormalux hosting
3) Tormalux customisation
4) Other
We need 2 pages in total:
1) Main landing page
This is the home page. It will need to clearly indicate our services and our key selling features.
Services:
* Tormalux support
* Tormalux hosting
* Tormalux customisation
Key Selling Features:
* Australian based
* PCI complaint
* 10+ years of dialler and call centre experience
* we run a sister company which is a highly reputable 40 seat call centre, so we know first hand about call centre technology.
The main landing page will have an "about us" section with a few paragraphs about how we got started.
-------------------------------------------------------------------------
2) Contact page
All of our contact details will live on this page, as well as a contact form.
Other notes:
We will be self hosting the landing page.
We already have a domain name.
The design must be clean and incorporate our logo, as well as it's colours. (Logo attached)
We want a fully function HTML landing page, not just a "PSD" design.
The page must be mobile optimised.
Anyone using Tormalux software.

```html
<!DOCTYPE html>
<html lang="en">
<head>
<meta charset="utf-8">
<title>Corvane – Tormalux Dialler Support</title>
<link href="https://fonts.googleapis.com/css2?family=Kumbh+Sans:wght@400;500;600;700&family=Poppins:wght@400;500;600&display=swap" rel="stylesheet">
<style>
:root{
  --blue:#1a8fd6;
  --blue-dark:#0f6fae;
  --navy:#17324a;
  --teal:#22c09c;
  --ink:#333a40;
  --muted:#6d7479;
  --footer:#0e0f10;
  --white:#ffffff;
  --line:#c9ced2;
}
*{box-sizing:border-box;margin:0;padding:0}
html,body{width:1200px;height:3175px;overflow:hidden}
body{position:relative;font-family:"Poppins",sans-serif;color:var(--ink);background:var(--white)}
.abs{position:absolute}
h1,h2,h3,.brand,.quote-cta{font-family:"Kumbh Sans",sans-serif}

/* hero */
.hero-bg{left:0;top:0;width:1200px;height:641px;
  background:linear-gradient(100deg,#1d3a52 0%,#2b5a7c 45%,#4a7fa3 75%,#6b95b4 100%);
  clip-path:polygon(0 0,1200px 0,1200px 514px,0 641px)}
.hero-shade{left:0;top:0;width:1200px;height:641px;background:linear-gradient(90deg,rgba(10,25,40,.55),rgba(10,25,40,0) 60%);clip-path:polygon(0 0,1200px 0,1200px 514px,0 641px)}
.brand{left:83px;top:36px;color:var(--white);font-size:30px;font-weight:600;letter-spacing:.5px;line-height:36px}
.nav{top:42px;left:512px;font-size:16px;color:var(--white)}
.nav a{position:absolute;white-space:nowrap;color:var(--white);text-decoration:none}
.nav a.active{color:#3aaef0}
.hero-title{left:83px;top:216px;color:var(--white);font-weight:500;font-size:35px;line-height:50px}
.hero-title strong{display:block;font-weight:700;font-size:40px}
.hero-text{left:83px;top:328px;width:420px;color:var(--white);font-size:15px;line-height:29px}
.btn{display:inline-flex;align-items:center;justify-content:center;border-radius:24px;color:var(--white);font-family:"Poppins",sans-serif;font-weight:600;font-size:16px}
.btn-read{left:83px;top:438px;width:140px;height:44px;background:var(--blue)}
.btn-contact{left:233px;top:438px;width:150px;height:44px;background:var(--teal)}

.quote{left:753px;top:123px;width:366px;height:546px;background:var(--white);box-shadow:0 4px 20px rgba(0,0,0,.15)}
.field{position:absolute;left:45px;width:275px;height:45px;border:1px solid var(--line);font-size:13px;font-style:italic;color:#8a9095;padding:0 13px;display:flex;align-items:center;justify-content:space-between}
.field.area{height:79px;align-items:flex-start;padding-top:14px}
.quote-btn{position:absolute;left:45px;top:347px;width:197px;height:46px;background:var(--blue);color:var(--white);font-weight:600;font-size:17px;display:flex;align-items:center;justify-content:center}
.quote-cta{position:absolute;left:0;top:395px;width:366px;height:151px;background:var(--blue);color:var(--white);font-size:33px;font-weight:700;padding:70px 0 0 36px}

/* about */
.about-shape{left:80px;top:751px;width:259px;height:392px;background:var(--blue);clip-path:polygon(0 0,136px 0,150px 30px,259px 30px,259px 360px,222px 360px,259px 392px,0 392px)}
.about-photo{left:108px;top:783px;width:482px;height:324px;background:linear-gradient(120deg,#f4f6f8 0%,#dfe6ec 40%,#5c6f82 70%,#2e3e50 100%);box-shadow:0 6px 18px rgba(0,0,0,.12)}
.section-title{color:var(--blue);font-weight:600;font-size:42px}
.about-title{left:679px;top:782px}
.about-text{left:679px;top:843px;width:440px;font-size:16px;line-height:28.5px;color:var(--muted)}
.btn-learn{left:679px;top:1047px;width:167px;height:51px;background:var(--blue);border-radius:26px}

/* services */
.services{left:0;top:1242px;width:1200px;height:584px;background:linear-gradient(180deg,#1f92d8,#1b86cc)}
.services .section-title{color:var(--white);position:absolute;width:100%;text-align:center;top:80px}
.rule{position:absolute;width:70px;height:4px;left:565px}
.services .rule{top:155px;background:var(--white)}
.svc{position:absolute;top:213px;width:300px;text-align:center;color:var(--white)}
.svc-icon{width:132px;height:132px;border:3px solid var(--white);border-radius:50%;margin:0 auto;display:flex;align-items:center;justify-content:center}
.svc h3{font-size:22px;font-weight:700;margin-top:20px}
.svc p{font-size:13px;line-height:22px;width:220px;margin:14px auto 0;color:#e2f1fb}
.arrow{position:absolute;top:340px}

/* features */
.features-title{left:0;top:1870px;width:1200px;text-align:center}
.features-rule{top:1933px;background:var(--blue)}
.feat-icon{left:85px;width:72px;height:72px;border:3px solid var(--blue);border-radius:50%;display:flex;align-items:center;justify-content:center}
.feat-text{left:193px;font-size:19px;line-height:37px;color:var(--ink)}
.frame{left:633px;top:2010px;width:477px;height:336px;border:2px solid #9aa1a6}
.frame-gap{left:700px;top:2000px;width:340px;height:356px;background:var(--white)}
.frame-gap2{left:623px;top:2060px;width:497px;height:236px;background:var(--white)}
.feat-photo{left:641px;top:2021px;width:460px;height:313px;background:linear-gradient(160deg,#d9c9b6 0%,#9ea7ad 45%,#5b6670 75%,#e6e9ec 100%)}

/* cta */
.cta{left:0;top:2493px;width:1200px;height:336px;background:linear-gradient(180deg,#1c8fd6,#1780c6);text-align:center;color:var(--white)}
.cta h2{font-size:41px;font-weight:600;margin-top:52px}
.cta p{font-size:20px;line-height:40px;margin-top:22px}
.btn-cta{position:absolute;left:508px;top:230px;width:220px;height:60px;background:var(--white);color:var(--blue);border-radius:30px;font-size:21px;font-weight:500;display:flex;align-items:center;justify-content:center}

/* footer */
.footer{left:0;top:2829px;width:1200px;height:281px;background:var(--footer);color:var(--white)}
.footer h4{position:absolute;top:46px;font-size:19px;font-weight:600}
.footer ul{position:absolute;top:96px;list-style:none;font-size:14px;line-height:32px}
.contact-item{position:absolute;left:83px;display:flex;gap:20px;font-size:14px;line-height:24px}
.news-text{position:absolute;left:870px;top:92px;width:250px;font-size:13.5px;line-height:27px}
.news-input{position:absolute;left:870px;top:185px;width:249px;height:42px;background:var(--white);display:flex;font-size:12px;color:#666}
.news-input span{flex:1;padding:13px 12px}
.news-input b{width:44px;background:var(--blue);display:flex;align-items:center;justify-content:center}
.copyright{left:0;top:3110px;width:1200px;height:65px;background:var(--blue);color:var(--white);font-size:15px;display:flex;align-items:center;justify-content:center}
</style>
</head>
<body>

<!-- Hero -->
<div class="abs hero-bg" role="img" aria-label="Smiling call centre agent wearing a headset at a desk"></div>
<div class="abs hero-shade"></div>
<div class="abs brand">Corvane</div>
<nav class="abs nav">
  <a class="active" style="left:0">Home</a>
  <a style="left:95px">About Us</a>
  <a style="left:212px">Services</a>
  <a style="left:326px">Features</a>
  <a style="left:442px">Contact Us</a>
  <a style="left:566px;top:2px"><svg width="16" height="16" viewBox="0 0 16 16"><circle cx="6.5" cy="6.5" r="5" fill="none" stroke="#fff" stroke-width="2"/><line x1="10.5" y1="10.5" x2="15" y2="15" stroke="#fff" stroke-width="2"/></svg></a>
</nav>
<h1 class="abs hero-title">We Offer Instant &amp; Quality<strong>Customer Service!</strong></h1>
<p class="abs hero-text">At vero eos et accusamus et iusto odio dignissimos ducimus qui blanditiis praesentium voluptatum deleniti atque corrupti quos dolores</p>
<a class="abs btn btn-read">Read More</a>
<a class="abs btn btn-contact">Contact Us</a>

<form class="abs quote">
  <div class="field" style="top:36px">Name</div>
  <div class="field" style="top:89px">Email</div>
  <div class="field" style="top:142px">Phone Number</div>
  <div class="field" style="top:195px">Tormalux Support <svg width="10" height="7" viewBox="0 0 10 7"><path d="M0 0h10L5 7z" fill="#8a9095"/></svg></div>
  <div class="field area" style="top:247px">Description</div>
  <div class="quote-btn">Get A Quote</div>
  <div class="quote-cta">Get A Free Quote</div>
</form>

<!-- About -->
<div class="abs about-shape"></div>
<div class="abs about-photo" role="img" aria-label="Support consultant with headset working at a laptop in an office"></div>
<h2 class="abs section-title about-title">About Us</h2>
<p class="abs about-text">Sed ut perspiciatis unde omnis iste natus error sit voluptatem accusantium doloremque laudantium, totam rem aperiam, eaque ipsa quae ab illo inventore veritatis et quasi architecto beatae vitae dicta sunt explicabo. Nemo enim ipsam voluptatem quia voluptas sit aspernatur aut odit aut fugit</p>
<a class="abs btn btn-learn">Learn More</a>

<!-- Services -->
<section class="abs services" role="img" aria-label="Blue tinted call centre office backdrop">
  <h2 class="section-title">Services</h2>
  <div class="rule"></div>
  <svg class="arrow" style="left:22px" width="22" height="34" viewBox="0 0 22 34"><path d="M18 2L4 17l14 15" fill="none" stroke="#fff" stroke-width="2.5"/></svg>
  <svg class="arrow" style="left:1136px" width="22" height="34" viewBox="0 0 22 34"><path d="M4 2l14 15L4 32" fill="none" stroke="#fff" stroke-width="2.5"/></svg>

  <div class="svc" style="left:104px">
    <div class="svc-icon"><svg width="60" height="60" viewBox="0 0 60 60" fill="none" stroke="#fff" stroke-width="2.5"><circle cx="30" cy="20" r="9"/><circle cx="30" cy="20" r="3"/><path d="M6 30v14l12 12M54 30v14L42 56M18 44l-6-10M42 44l6-10"/></svg></div>
    <h3>Tormalux Support</h3>
    <p>Sed ut perspiciatis unde omnis iste natus error sit voluptatem accusantium doloremque dantium</p>
  </div>
  <div class="svc" style="left:447px">
    <div class="svc-icon"><svg width="60" height="60" viewBox="0 0 60 60" fill="none" stroke="#fff" stroke-width="2.5"><rect x="12" y="6" width="36" height="10" rx="2"/><rect x="12" y="22" width="36" height="10" rx="2"/><rect x="12" y="38" width="36" height="10" rx="2"/><circle cx="18" cy="11" r="1.5"/><circle cx="18" cy="27" r="1.5"/><circle cx="18" cy="43" r="1.5"/><path d="M30 48v8M20 56h20"/></svg></div>
    <h3>Tormalux Hosting</h3>
    <p>Sed ut perspiciatis unde omnis iste natus error sit voluptatem accusantium doloremque dantium</p>
  </div>
  <div class="svc" style="left:771px">
    <div class="svc-icon"><svg width="60" height="60" viewBox="0 0 60 60" fill="none" stroke="#fff" stroke-width="2.5"><path d="M10 50l26-26M40 8a10 10 0 0 0 12 12l-6 6-12-12z"/><path d="M50 50L20 20l-4-8-6-2-2 2 2 6 8 4M44 44l8 8"/></svg></div>
    <h3>Tormalux Customisation</h3>
    <p>Sed ut perspiciatis unde omnis iste natus error sit voluptatem accusantium doloremque dantium</p>
  </div>
</section>

<!-- Features -->
<h2 class="abs section-title features-title">Features</h2>
<div class="rule features-rule"></div>

<div class="abs feat-icon" style="top:1985px"><svg width="34" height="34" viewBox="0 0 34 34" fill="none" stroke="#1a8fd6" stroke-width="2"><rect x="3" y="5" width="28" height="24" rx="2"/><line x1="3" y1="11" x2="31" y2="11"/><circle cx="17" cy="20" r="5"/></svg></div>
<div class="abs feat-text" style="top:2002px">Australian based</div>

<div class="abs feat-icon" style="top:2082px"><svg width="34" height="34" viewBox="0 0 34 34" fill="none" stroke="#1a8fd6" stroke-width="2"><rect x="8" y="15" width="18" height="14" rx="2"/><path d="M12 15v-4a5 5 0 0 1 10 0v4"/><circle cx="17" cy="22" r="2"/></svg></div>
<div class="abs feat-text" style="top:2094px">PCI complaint</div>

<div class="abs feat-icon" style="top:2179px"><svg width="34" height="34" viewBox="0 0 34 34" fill="none" stroke="#1a8fd6" stroke-width="2"><circle cx="17" cy="12" r="6"/><path d="M6 31c1-7 6-11 11-11s10 4 11 11"/><path d="M10 12a7 7 0 0 1 14 0"/></svg></div>
<div class="abs feat-text" style="top:2185px">10+ years of dialler and call centre<br>experience</div>

<div class="abs feat-icon" style="top:2279px"><svg width="34" height="34" viewBox="0 0 34 34" fill="none" stroke="#1a8fd6" stroke-width="2"><path d="M6 20v-4a11 11 0 0 1 22 0v4"/><rect x="4" y="18" width="6" height="9" rx="2"/><rect x="24" y="18" width="6" height="9" rx="2"/><path d="M27 27c0 3-3 4-7 4"/></svg></div>
<div class="abs feat-text" style="top:2283px">we run a sister company which is a<br>highly reputable 40 seat call centre,<br>so we know first hand about<br>call centre technology.</div>

<div class="abs frame"></div>
<div class="abs frame-gap"></div>
<div class="abs frame-gap2"></div>
<div class="abs feat-photo" role="img" aria-label="Smiling agent with headset in a busy call centre"></div>

<!-- Call to action -->
<section class="abs cta" role="img" aria-label="Blue tinted backdrop of a call centre agent">
  <h2>Get Your Free Consulting</h2>
  <p>Lorem ipsum dolor sit amet, consectetur adipiscing elit, sed do eiusmod<br>tempor incididunt ut labore et dolore magna aliqua.</p>
  <a class="btn-cta">Contact Us</a>
</section>

<!-- Footer -->
<footer class="abs footer">
  <h4 style="left:83px">Contact Us</h4>
  <div class="contact-item" style="top:96px"><svg width="14" height="20" viewBox="0 0 14 20"><path d="M7 0a7 7 0 0 0-7 7c0 5 7 13 7 13s7-8 7-13a7 7 0 0 0-7-7z" fill="#fff"/><circle cx="7" cy="7" r="2.5" fill="#0e0f10"/></svg><span>No.72, Harbour Lane,<br>Westfield, QLD 4102</span></div>
  <div class="contact-item" style="top:163px"><svg width="16" height="16" viewBox="0 0 16 16"><path d="M3 1l3 3-2 2c1 2 3 4 6 6l2-2 3 3-2 2C7 15 1 9 1 3z" fill="#fff"/></svg><span>+61-400-555-018</span></div>
  <div class="contact-item" style="top:205px"><svg width="16" height="12" viewBox="0 0 16 12"><rect width="16" height="12" fill="#fff"/><path d="M0 0l8 6 8-6" fill="none" stroke="#0e0f10" stroke-width="1.5"/></svg><span>hello@corvane.com</span></div>

  <h4 style="left:415px">Links</h4>
  <ul style="left:415px"><li>Home</li><li>About Us</li><li>Services</li><li>Features</li><li>Contact Us</li></ul>

  <h4 style="left:601px">Services</h4>
  <ul style="left:601px;line-height:34px"><li>Tormalux Support</li><li>Tormalux hosting</li><li>Tormalux Customisation</li></ul>

  <h4 style="left:870px">Newsletter</h4>
  <p class="news-text">But I must explain to you how all this mistaken idea of enouncing pleasure and praising.</p>
  <div class="news-input"><span>Enter your email address</span><b><svg width="14" height="12" viewBox="0 0 14 12"><path d="M0 6h12M7 1l5 5-5 5" fill="none" stroke="#fff" stroke-width="2"/></svg></b></div>
</footer>
<div class="abs copyright">© 2018 Copyrights | All Rights Reserved</div>

</body>
</html>
```